Local massage therapist needs some new marketing material

Hi there! I am a massage therapist here in Denver, CO in Alder Bend(shopping and art district) of the city. My business is called Lumo Bodywork of Denver. My practice has an eastern influence and I do reflexology, thai massage and use Chinese herbs, etc. I know all my clients and pay close attention to details. I am also very respectful of tradition and it shows in how I work. I tend to like modern, clean, fun, Asian designs. I am wanting a new business card and brochure. I have a logo and branding for my business that I want used in the design. Currently, the sign for my building is purple and I think my logo was designed to be purple. I will attach pictures of it and can send whatever files are necessary so it can be integrated into the brochure, etc. I like the purple but open to using other colors as well. Thanks!
My website is lumobodyworkofdenver.example where info can be gathered about me and services/fees for brochure.
Updates

Just increased budget. Please see new feedback in discussion thread.

Thanks!

                                       HEY ALL,

Just wanted to let you know that I made a change to my website. It is on the Prices Page. I no longer have the frequent  flyer prices but I added discounts. Let me know if you have any questions. Thanks so much!

Target Market(s)

healthy, urban, educated, upper middle class, yogis

Industry/Entity Type

Marketing

Requirements
Must have
• logo stays purple
Should not have
• not too busy

```html
<!DOCTYPE html>
<html lang="en">
<head>
<meta charset="utf-8">
<title>Lumo Bodywork of Denver — Business Card Concepts</title>
<link rel="stylesheet" href="https://fonts.googleapis.com/css2?family=Tinos:wght@400&display=swap">
<style>
  :root {
    --sheet: #000000;
    --purple: #5a2784;
    --purple-deep: #4a1f70;
    --purple-soft: #7a4aa3;
    --lilac: #b79bcf;
    --grey: #c8c8c8;
    --grey-light: #e4e4e4;
    --white: #ffffff;
    --serif: "Tinos", "Times New Roman", serif;
  }
  * { box-sizing: border-box; margin: 0; padding: 0; }
  html, body { width: 849px; height: 1200px; overflow: hidden; background: var(--sheet); }
  .sheet { position: relative; width: 849px; height: 1200px; font-family: var(--serif); }

  .card { position: absolute; width: 366px; height: 218px; overflow: hidden; }
  .pos-1 { left: 51px;  top: 51px; }
  .pos-2 { left: 433px; top: 51px; }
  .pos-3 { left: 51px;  top: 306px; }
  .pos-4 { left: 433px; top: 306px; }
  .pos-5 { left: 51px;  top: 560px; }
  .pos-6 { left: 433px; top: 560px; }
  .pos-7 { left: 238px; top: 835px; }

  .bg-purple { background: var(--purple); }
  .bg-white { background: var(--white); }

  .brand { position: absolute; display: flex; align-items: center; gap: 10px; }
  .brand-mark { width: 26px; height: 26px; border-radius: 50%; border: 1.5px solid currentColor; flex: none; }
  .brand-name { font-size: 15px; letter-spacing: 2.5px; text-transform: uppercase; line-height: 1.15; }
  .on-purple { color: var(--white); }
  .on-white { color: var(--purple); }

  .url { position: absolute; font-size: 10.5px; letter-spacing: .3px; }
  .info { position: absolute; font-size: 9.5px; line-height: 1.45; }
  .info p { white-space: nowrap; }
  .icon { width: 13px; height: 13px; fill: currentColor; display: block; }

  .decor { position: absolute; }

  /* Card 1 */
  .c1-decor { right: -30px; top: 20px; width: 180px; height: 180px; border-radius: 50%;
    background: radial-gradient(circle, rgba(255,255,255,.09), rgba(255,255,255,0) 70%); }

  /* Card 2 */
  .c2-strip { position: absolute; left: 20px; top: 0; width: 30px; height: 100%; background: var(--white);
    display: flex; flex-direction: column; align-items: center; gap: 17px; padding-top: 30px; color: var(--purple); }
  .c2-info { left: 62px; top: 26px; color: var(--white); }
  .c2-info p { margin-bottom: 4px; }
  .c2-hours { left: 62px; top: 160px; color: var(--white); }

  /* Card 3 */
  .c3-main { position: absolute; left: 8px; top: 8px; width: 240px; height: 152px; background: var(--purple); }
  .c3-side { position: absolute; left: 256px; top: 8px; width: 102px; height: 152px; background: var(--purple); }
  .c3-foot { position: absolute; left: 8px; top: 168px; width: 350px; height: 42px; background: var(--grey-light); }

  /* Card 4 */
  .c4-panel { position: absolute; left: 52px; top: 0; width: 262px; height: 218px; background: var(--purple); }
  .c4-info { left: 66px; top: 24px; color: var(--white); }
  .c4-row { display: flex; align-items: center; gap: 8px; margin-bottom: 6px; }

  /* Card 5 */
  .c5-band { position: absolute; left: 0; top: 132px; width: 100%; height: 34px; background: var(--grey); }
  .c5-line { position: absolute; left: 0; top: 146px; width: 100%; height: 4px; background: var(--white); }
  .c5-decor { right: 0; top: 0; width: 170px; height: 120px;
    background: linear-gradient(135deg, rgba(183,155,207,0) 20%, rgba(183,155,207,.35) 100%); }

  /* Card 6 */
  .c6-band { position: absolute; left: 0; top: 76px; width: 100%; height: 64px; background: var(--grey); display: flex; }
  .c6-cell { flex: 1; display: flex; flex-direction: column; align-items: center; justify-content: center; gap: 4px;
    font-size: 8px; color: var(--purple-deep); border-right: 1px solid var(--white); text-align: center; }
  .c6-cell:last-child { border-right: none; }
  .c6-cell .icon { width: 16px; height: 16px; }
  .c6-hours { left: 150px; top: 160px; color: var(--white); }

  /* Card 7 */
  .c7-bottom { position: absolute; left: 0; top: 130px; width: 100%; height: 88px; background: var(--purple); }
  .c7-rail { position: absolute; right: 0; top: 0; width: 26px; height: 100%; background: var(--purple-deep);
    display: flex; flex-direction: column; align-items: center; justify-content: space-around; padding: 68px 0 8px; }
  .c7-dot { width: 18px; height: 18px; border-radius: 50%; background: var(--grey); color: var(--purple);
    display: flex; align-items: center; justify-content: center; }
  .c7-dot .icon { width: 11px; height: 11px; }
  .c7-brand { left: 28px; top: 16px; }
  .c7-info { left: 72px; top: 70px; color: var(--purple-deep); }
  .c7-lower { left: 72px; top: 140px; color: var(--white); }
</style>
</head>
<body>
<svg width="0" height="0" style="position:absolute" aria-hidden="true">
  <defs>
    <symbol id="i-home" viewBox="0 0 24 24"><path d="M12 3 2 12h3v9h5v-6h4v6h5v-9h3z"/></symbol>
    <symbol id="i-phone" viewBox="0 0 24 24"><path d="M6.6 10.8a15 15 0 0 0 6.6 6.6l2.2-2.2a1 1 0 0 1 1-.25 11.4 11.4 0 0 0 3.6.57 1 1 0 0 1 1 1V20a1 1 0 0 1-1 1A17 17 0 0 1 3 4a1 1 0 0 1 1-1h3.5a1 1 0 0 1 1 1c0 1.250.2 2.450.57 3.6a1 1 0 0 1-.25 1z"/></symbol>
    <symbol id="i-mail" viewBox="0 0 24 24"><path d="M3 5h18v14H3zm2 2v.4l7 4.6 7-4.6V7zm0 2.8V17h14V9.8l-7 4.6z"/></symbol>
    <symbol id="i-info" viewBox="0 0 24 24"><path d="M12 2a10 10 0 1 0 0 20 10 10 0 0 0 0-20zm1 15h-2v-6h2zm0-8h-2V7h2z"/></symbol>
  </defs>
</svg>

<main class="sheet">

  <!-- Concept A front -->
  <section class="card pos-1 bg-purple">
    <div class="decor c1-decor" role="img" aria-label="faint decorative motif"></div>
    <div class="brand on-purple" style="left:34px; top:84px;">
      <span class="brand-mark"></span>
      <span class="brand-name">Lumo Bodywork<br>of Denver</span>
    </div>
    <p class="url on-purple" style="left:34px; top:150px;">www.lumobodyworkofdenver.example</p>
  </section>

  <!-- Concept A back -->
  <section class="card pos-2 bg-purple">
    <div class="c2-strip">
      <svg class="icon"><use href="#i-home"/></svg>
      <svg class="icon"><use href="#i-phone"/></svg>
      <svg class="icon"><use href="#i-mail"/></svg>
      <svg class="icon"><use href="#i-info"/></svg>
    </div>
    <div class="info c2-info">
      <p>1480 E 4th Ave, Denver, CO 80218,<br>P: 303.555.0142</p>
      <p>+91-0000000000, +91-0000000000</p>
      <p>info@lumobodyworkofdenver.example</p>
    </div>
    <div class="info c2-hours">
      <p>(Appointments required) No walk-ins please</p>
      <p>Tues - Fri 10am - 9pm Sat 10am-5pm</p>
    </div>
  </section>

  <!-- Concept B front -->
  <section class="card pos-3 bg-white">
    <div class="c3-main"></div>
    <div class="c3-side"></div>
    <div class="c3-foot"></div>
    <div class="brand on-purple" style="left:30px; top:68px;">
      <span class="brand-mark"></span>
      <span class="brand-name">Lumo Bodywork<br>of Denver</span>
    </div>
    <p class="url on-white" style="left:30px; top:183px;">www.lumobodyworkofdenver.example</p>
  </section>

  <!-- Concept B back -->
  <section class="card pos-4 bg-white">
    <div class="c4-panel"></div>
    <div class="info c4-info">
      <div class="c4-row"><svg class="icon"><use href="#i-home"/></svg><p>1480 E 4th Ave, Denver, CO 80218,<br>P: 303.555.0142</p></div>
      <div class="c4-row"><svg class="icon"><use href="#i-phone"/></svg><p>+91-0000000000, +91-0000000000</p></div>
      <div class="c4-row"><svg class="icon"><use href="#i-mail"/></svg><p>info@lumobodyworkofdenver.example</p></div>
      <div class="c4-row" style="margin-top:28px;"><svg class="icon"><use href="#i-info"/></svg><p>(Appointments required) No walk-ins please<br>Tues - Fri 10am - 9pm Sat 10am-5pm</p></div>
    </div>
  </section>

  <!-- Concept C front -->
  <section class="card pos-5 bg-purple">
    <div class="decor c5-decor" role="img" aria-label="soft flowing swirl decoration"></div>
    <div class="c5-band"></div>
    <div class="c5-line"></div>
    <div class="brand on-purple" style="left:26px; top:66px;">
      <span class="brand-mark"></span>
      <span class="brand-name">Lumo Bodywork<br>of Denver</span>
    </div>
    <p class="url on-purple" style="left:26px; top:180px;">www.lumobodyworkofdenver.example</p>
  </section>

  <!-- Concept C back -->
  <section class="card pos-6 bg-purple">
    <div class="c6-band">
      <div class="c6-cell"><svg class="icon"><use href="#i-home"/></svg><p>1480 E 4th Ave,<br>Denver, CO 80218<br>P: 303.555.0142</p></div>
      <div class="c6-cell"><svg class="icon"><use href="#i-phone"/></svg><p>+91-0000000000<br>+91-0000000000</p></div>
      <div class="c6-cell"><svg class="icon"><use href="#i-mail"/></svg><p>info@lumobodywork<br>ofdenver.example</p></div>
    </div>
    <div class="info c6-hours">
      <p>(Appointments required) No walk-ins please</p>
      <p>Tues - Fri 10am - 9pm Sat 10am-5pm</p>
    </div>
  </section>

  <!-- Concept D single-sided -->
  <section class="card pos-7 bg-white">
    <div class="c7-bottom"></div>
    <div class="c7-rail">
      <span class="c7-dot"><svg class="icon"><use href="#i-home"/></svg></span>
      <span class="c7-dot"><svg class="icon"><use href="#i-phone"/></svg></span>
      <span class="c7-dot"><svg class="icon"><use href="#i-mail"/></svg></span>
      <span class="c7-dot"><svg class="icon"><use href="#i-info"/></svg></span>
    </div>
    <div class="brand on-white c7-brand">
      <span class="brand-mark"></span>
      <span class="brand-name">Lumo Bodywork<br>of Denver</span>
    </div>
    <div class="info c7-info">
      <p>1480 E 4th Ave, Denver, CO 80218</p>
      <p>P: 303.555.0142</p>
      <p>+91-0000000000, +91-0000000000</p>
    </div>
    <div class="info c7-lower">
      <p>info@lumobodyworkofdenver.example</p>
      <p>www.lumobodyworkofdenver.example</p>
      <p style="margin-top:6px;">(Appointments required) No walk-ins please</p>
      <p>Tues - Fri 10am - 9pm Sat 10am-5pm</p>
    </div>
  </section>

</main>
</body>
</html>
```